Visit card

Industry/Entity Type

Health Care

Contact Information for Business Card

O VITALIS SYSTEMS
Odile Brevard - chef de Projet

Requirements
Must have
• 318 Gaston Lemaire Street 59710 BÉTHUNE Tel: 33 (0) 327 481 605 Mobile: 06 42 19 37 64 Web: www.quorvexsystems.example Contact: o.brevard@o-vitalissystems.example
Should not have
• Respect for color

```html
<!DOCTYPE html>
<html lang="fr">
<head>
<meta charset="utf-8">
<title>O Vitalis Systems – Cartes de visite</title>
<link rel="stylesheet" href="https://fonts.googleapis.com/css2?family=Lato:wght@400;700;900&display=swap">
<style>
  :root {
    --bg: #1b1b1b;
    --card: #1f1f1f;
    --card-edge: #2a2a2a;
    --red: #e8212e;
    --white: #ffffff;
    --soft: #e6e6e6;
  }
  * { box-sizing: border-box; margin: 0; padding: 0; }
  html, body { width: 1200px; height: 900px; overflow: hidden; background: var(--bg); }
  body { font-family: "Lato", sans-serif; color: var(--white); position: relative; }

  .card {
    position: absolute;
    left: 250px;
    width: 700px;
    height: 400px;
    background: var(--card);
    border: 1px solid var(--card-edge);
    border-radius: 3px;
  }
  .card--front { top: 35px; }
  .card--back  { top: 465px; }

  .brand {
    position: absolute;
    display: flex;
    align-items: center;
    gap: 22px;
  }
  .card--front .brand { left: 50%; top: 50%; transform: translate(-50%, -50%); }
  .card--back .brand  { left: 60px; top: 150px; }

  .brand__mark {
    width: 90px; height: 90px;
    border: 14px solid var(--white);
    border-radius: 50%;
    flex: none;
  }
  .brand__name {
    font-weight: 900;
    color: var(--white);
    line-height: 1;
  }
  .brand__line1 { display: block; font-size: 44px; letter-spacing: 1px; }
  .brand__line2 { display: block; font-size: 18px; letter-spacing: 7px; margin-top: 6px; }

  .divider {
    position: absolute;
    left: 395px; top: 110px;
    width: 2px; height: 190px;
    background: var(--soft);
  }

  .contact {
    position: absolute;
    left: 425px; top: 108px;
    font-size: 15px;
    color: var(--soft);
    line-height: 1.35;
  }
  .contact__name {
    color: var(--red);
    font-weight: 700;
    font-size: 22px;
    text-transform: uppercase;
    letter-spacing: 0.5px;
  }
  .contact__role { font-size: 15px; margin-bottom: 10px; }
  .contact__address { margin-bottom: 10px; }
  .contact__list { list-style: none; }
  .contact__list li { display: flex; align-items: center; gap: 8px; white-space: nowrap; }
  .contact__list svg { width: 11px; height: 11px; flex: none; }
</style>
</head>
<body>

<section class="card card--front" aria-label="Recto">
  <div class="brand">
    <span class="brand__mark" aria-hidden="true"></span>
    <span class="brand__name">
      <span class="brand__line1">O VITALIS</span>
      <span class="brand__line2">SYSTEMS</span>
    </span>
  </div>
</section>

<section class="card card--back" aria-label="Verso">
  <div class="brand">
    <span class="brand__mark" aria-hidden="true"></span>
    <span class="brand__name">
      <span class="brand__line1">O VITALIS</span>
      <span class="brand__line2">SYSTEMS</span>
    </span>
  </div>

  <span class="divider" aria-hidden="true"></span>

  <div class="contact">
    <p class="contact__name">Odile Brevard</p>
    <p class="contact__role">Chef de Projet</p>
    <p class="contact__address">318 Gaston Lemaire Street<br>59710 BÉTHUNE</p>
    <ul class="contact__list">
      <li>
        <svg viewBox="0 0 12 12" aria-hidden="true"><path d="M2.5 1 L4.5 1 L5 3.5 L3.8 4.5 Q5 7 7.5 8.2 L8.5 7 L11 7.5 L11 9.5 Q11 11 9.5 11 Q1 10 1 2.5 Q1 1 2.5 1Z" fill="var(--red)"/></svg>
        +33 (0) 327 481 605
      </li>
      <li>
        <svg viewBox="0 0 12 12" aria-hidden="true"><rect x="3" y="0.5" width="6" height="11" rx="1" fill="none" stroke="var(--red)" stroke-width="1.2"/><circle cx="6" cy="9.5" r="0.7" fill="var(--red)"/></svg>
        06 42 19 37 64
      </li>
      <li>
        <svg viewBox="0 0 12 12" aria-hidden="true"><g fill="none" stroke="var(--red)" stroke-width="1"><circle cx="6" cy="6" r="5"/><ellipse cx="6" cy="6" rx="2.2" ry="5"/><line x1="1" y1="6" x2="11" y2="6"/></g></svg>
        www.quorvexsystems.example
      </li>
      <li>
        <svg viewBox="0 0 12 12" aria-hidden="true"><g fill="none" stroke="var(--red)" stroke-width="1.1"><rect x="0.8" y="2.5" width="10.4" height="7" rx="0.8"/><polyline points="1,3 6,7 11,3"/></g></svg>
        o.brevard@o-vitalissystems.example
      </li>
    </ul>
  </div>
</section>

</body>
</html>
```